Business Card Design for Software Development Company

I am looking for a business card design the incorporates my new logo (attached below).

Key information to include:
Name: Martin Quelbrook
Title: CEO
Email: martin@brightwellcivic.example
Phone: 555-218-9403
Website: www.brightwellcivic.example

NOTE: This design should be easy to edit so that we can order cards for different members of our team.

```html
<!DOCTYPE html>
<html lang="en">
<head>
<meta charset="utf-8">
<title>Brightwell Labs Business Card</title>
<link href="https://fonts.googleapis.com/css2?family=Montserrat:wght@400;500;600;700&display=swap" rel="stylesheet">
<style>
  :root {
    --bg: #e6e4e5;
    --paper: #ffffff;
    --navy: #343a55;
    --orange: #e87f3a;
    --ink: #1f1f24;
    --slate: #6f7a9b;
    --white: #ffffff;
  }
  * { margin: 0; padding: 0; box-sizing: border-box; }
  html, body {
    width: 1200px; height: 1108px; overflow: hidden;
    background: var(--bg);
    font-family: "Montserrat", sans-serif;
  }
  .card { position: absolute; left: 229px; width: 755px; }
  .card--front { top: 56px; height: 462px; background: var(--paper); }
  .card--back { top: 575px; height: 444px; background: var(--slate); }

  .brand { position: absolute; display: flex; align-items: center; }
  .brand__dot { border-radius: 50%; flex: none; }
  .brand__name { font-weight: 700; white-space: nowrap; letter-spacing: -0.5px; }
  .brand__sub { position: absolute; right: 0; font-weight: 700; white-space: nowrap; letter-spacing: 0.3px; }

  .card--front .brand { left: 92px; top: 236px; }
  .card--front .brand__dot { width: 22px; height: 22px; background: var(--orange); margin-right: 8px; }
  .card--front .brand__name { font-size: 27px; color: var(--navy); }
  .card--front .brand__sub { top: 34px; font-size: 4.5px; color: var(--navy); }

  .divider { position: absolute; left: 373px; top: 177px; width: 1.5px; height: 148px; background: var(--orange); }

  .contact { position: absolute; left: 387px; top: 178px; }
  .contact__name { font-size: 29px; font-weight: 600; color: var(--orange); line-height: 1; margin-left: 3px; }
  .contact__title { font-size: 17px; color: var(--ink); margin-top: 10px; line-height: 1; }
  .contact__list { list-style: none; margin-top: 8px; }
  .contact__item { display: flex; align-items: center; font-size: 18px; color: var(--ink); height: 29.5px; }
  .contact__icon { width: 15px; height: 15px; margin-right: 9px; flex: none; }

  .address { position: absolute; left: 0; right: 0; top: 397px; text-align: center; font-size: 17px; color: var(--ink); }

  .card--back .brand { left: 84px; top: 200px; }
  .card--back .brand__dot { width: 54px; height: 54px; background: var(--orange); margin-right: 16px; }
  .card--back .brand__name { font-size: 62px; color: var(--white); }
  .card--back .brand__sub { top: 80px; font-size: 9.5px; color: var(--white); }
</style>
</head>
<body>
  <section class="card card--front">
    <div class="brand">
      <span class="brand__dot"></span>
      <span class="brand__name">Brightwell Labs</span>
      <span class="brand__sub">A DIVISION OF BRIGHTWELL CIVIC</span>
    </div>
    <div class="divider"></div>
    <div class="contact">
      <p class="contact__name">Martin Quelbrook</p>
      <p class="contact__title">CEO</p>
      <ul class="contact__list">
        <li class="contact__item">
          <svg class="contact__icon" viewBox="0 0 16 16"><path d="M4 1.5l2.3 3-1.4 1.6c.8 1.9 2.5 3.7 4.6 4.6l1.6-1.4 3 2.3-1.6 2.6C7.5 14 2 8.5 1.4 3.1z" fill="var(--orange)"/></svg>
          555-218-9403
        </li>
        <li class="contact__item">
          <svg class="contact__icon" viewBox="0 0 16 16"><rect x="1.5" y="4" width="13" height="9" fill="var(--orange)"/><path d="M1.5 4.5l6.5 4.5 6.5-4.5" fill="none" stroke="var(--paper)" stroke-width="1.2"/></svg>
          martin@brightwellcivic.example
        </li>
        <li class="contact__item">
          <svg class="contact__icon" viewBox="0 0 16 16"><circle cx="8" cy="8" r="6.5" fill="var(--orange)"/><path d="M1.5 8h13M8 1.5c-2.5 3-2.5 10 0 13M8 1.5c2.5 3 2.5 10 0 13" fill="none" stroke="var(--paper)" stroke-width="1"/></svg>
          www.brightwellcivic.example
        </li>
      </ul>
    </div>
    <p class="address">418 Harbor Lane, #112 Fairmont, OH 43099</p>
  </section>

  <section class="card card--back">
    <div class="brand">
      <span class="brand__dot"></span>
      <span class="brand__name">Brightwell Labs</span>
      <span class="brand__sub">A DIVISION OF BRIGHTWELL CIVIC</span>
    </div>
  </section>
</body>
</html>
```